UK Online Auction Site needs a clever design

We need a contemporary landing page and registration page design for a UK auction website, that look equally at home on PC's and tablets . The design should be fresh, bright, clean, professional, robust, and familiar. We would like to see something clever but functional.

Online

```html
<!DOCTYPE html>
<html lang="en">
<head>
<meta charset="utf-8">
<title>Bidwell – Online Store</title>
<link rel="stylesheet" href="https://fonts.googleapis.com/css2?family=Source+Sans+3:wght@400;600;700&family=Marcellus&family=Quicksand:wght@300;400&display=swap">
<style>
:root{
  --blue:#1a8fd6;
  --blue-dark:#0d6fb3;
  --blue-text:#2086c8;
  --ink:#333;
  --muted:#666;
  --line:#d9d9d9;
  --page:#f1f1f1;
  --white:#fff;
  --btn-dark:#444;
  --orange:#f27b21;
  --red:#e02b1f;
  --rust:#c8400a;
  --yellow:#f8d21a;
}
*{box-sizing:border-box;margin:0;padding:0}
html,body{width:838px;height:1200px;overflow:hidden}
body{background:var(--page);font-family:"Source Sans 3",sans-serif;color:var(--ink);position:relative;font-size:9px}
.abs{position:absolute}
.logo{left:91px;top:14px;width:86px;height:34px;display:flex;align-items:center;gap:5px;font-size:20px;font-weight:700;color:var(--blue)}
.logo-dot{width:10px;height:10px;border-radius:50%;background:var(--blue)}
.top-links{right:92px;top:11px;font-size:8px;color:#555;display:flex;gap:5px;align-items:center}
.top-links .cart{width:14px;height:11px}
.search{left:594px;top:34px;width:152px;height:17px;border:1px solid #ccc;background:var(--white);display:flex}
.search span{flex:1;font-style:italic;color:#999;font-size:8px;padding:3px 6px}
.search b{width:27px;background:#555;display:flex;align-items:center;justify-content:center}
.sidebar{left:91px;top:70px;width:154px;height:207px;border:2px solid #111;background:var(--white)}
.sidebar h2{background:linear-gradient(var(--blue),var(--blue-dark));color:var(--white);font-size:13px;font-weight:600;height:28px;line-height:28px;padding-left:11px}
.sidebar li{list-style:none;font-size:9px;color:#444;height:21px;line-height:21px;border-bottom:1px solid #e4e4e4;padding-left:11px}
.sidebar li::before{content:"›";color:var(--blue);font-weight:700;margin-right:7px}
.hero{left:258px;top:70px;width:490px;height:208px;border:2px solid #111;background:linear-gradient(#f6f6f6,#e4e4e4);overflow:hidden}
.hero .pct{left:30px;top:18px;font-family:Quicksand,sans-serif;color:var(--red);font-size:38px;font-weight:300}
.hero .pct small{font-size:20px;color:#444}
.hero .smart{left:27px;top:66px;font-family:Quicksand,sans-serif;font-size:20px;color:#444}
.hero .cams{left:26px;top:86px;font-family:Quicksand,sans-serif;font-size:34px;color:var(--orange);font-weight:300}
.hero .hurry{left:30px;top:130px;font-family:Quicksand,sans-serif;font-size:11px;color:#333}
.hero .view{left:29px;top:163px;width:62px;height:17px;border-radius:9px;background:#333;color:#eee;font-size:8px;line-height:17px;text-align:center}
.hero .photo{left:208px;top:62px;width:252px;height:108px;border-radius:6px;background:linear-gradient(135deg,#4a4a4a,#111 60%,#2a5a8a)}
.hero .badge{left:360px;top:-36px;width:108px;height:96px;border-radius:50%;background:var(--red);color:var(--white);font-size:13px;text-align:center;padding-top:42px;line-height:18px}
.divider{left:91px;top:294px;width:657px;height:5px;background:linear-gradient(#e2e2e2,transparent);border-radius:50%}
.info{left:91px;top:325px;width:657px;height:166px;background:var(--white);border:1px solid var(--line)}
.col{position:absolute;top:0;height:100%}
.col h3{color:var(--blue-text);font-weight:400;font-size:13px;margin-top:10px}
.welcome{left:0;width:153px;padding-left:6px;border-right:1px solid var(--line)}
.welcome p{color:var(--muted);font-size:8px;line-height:17px;margin-top:2px}
.welcome li{list-style:none;font-size:8px;line-height:14.6px;color:#222}
.welcome li::before{content:"»";color:var(--blue);margin-right:6px}
.signin{left:153px;width:174px;padding-left:14px;border-right:1px solid var(--line)}
.signin p{color:var(--muted);font-size:8px;line-height:17px;margin-top:2px}
.signin .btn{margin-top:8px;width:128px;height:18px;border-radius:2px;background:linear-gradient(#3b8de0,#1b61b8);color:var(--white);font-weight:600;font-size:9px;text-align:center;line-height:18px}
.signin .reg{margin:8px 0 0 4px;font-size:8px;color:#444}
.confidence{left:327px;width:176px;padding-left:22px}
.conf-item{display:flex;gap:8px;margin-top:7px}
.conf-item svg{flex:none;margin-top:2px}
.conf-item b{font-weight:400;font-size:9px;display:block;color:#222}
.conf-item span{font-size:7px;color:var(--muted);line-height:10px;display:block}
.results{left:594px;top:334px;width:145px;height:148px;background:var(--rust);color:var(--white)}
.results h4{font-size:16px;font-weight:700;margin:8px 0 0 9px;padding-bottom:4px;border-bottom:1px dotted #f5a070;width:126px}
.results .ring{position:absolute;left:72px;top:40px;width:66px;height:66px;border-radius:50%;border:4px solid var(--white);background:var(--yellow);color:var(--rust);font-weight:700;font-size:11px;text-align:center;line-height:58px}
.results .num{position:absolute;left:9px;top:98px;font-size:19px;font-weight:700}
.results .strip{position:absolute;left:0;bottom:0;width:100%;height:26px;background:rgba(0,0,0,.45);font-size:10px;padding:7px 0 0 18px}
.bar{left:91px;width:658px;height:31px;background:linear-gradient(var(--blue),var(--blue-dark));color:var(--white);font-size:13px;font-weight:600;padding-left:9px;line-height:31px}
.bar .arrows{position:absolute;right:10px;top:7px;display:flex;gap:4px}
.bar .arrows i{width:17px;height:17px;border-radius:50%;background:#0b4f88;display:block}
.product{position:absolute;width:155px;text-align:center}
.product .pic{height:110px;border:1px solid var(--line);background:var(--white);display:flex;align-items:center;justify-content:center}
.product .pic i{display:block;width:110px;height:80px;border-radius:6px}
.product h5{color:var(--blue-text);font-size:10px;font-weight:600;margin-top:11px;letter-spacing:.3px}
.product p{font-size:8px;color:#555;line-height:14px;margin-top:2px}
.product .price{font-family:Marcellus,serif;color:var(--blue-dark);font-size:15px;letter-spacing:1px;margin-top:4px}
.product .btns{display:flex;justify-content:center;gap:15px;margin-top:7px}
.product .btns span{width:55px;height:22px;line-height:22px;font-size:9px;border:1px solid #bbb;background:linear-gradient(#fff,#e9e9e9);color:#333}
.product .btns .add{background:var(--btn-dark);color:#f3f3f3;border-color:#222}
.footer{left:0;top:1114px;width:838px;height:86px;background:#f7f7f7;border-top:1px solid #e6e6e6}
.cards{left:94px;top:1140px;display:flex;gap:2px}
.cards i{display:block;width:26px;height:17px;border:1px solid #999;background:#dfe6ef}
.cards i:first-child{width:55px}
.copy{left:94px;top:1172px;font-size:8px;color:#555}
.copy b{color:#222}
.news{left:413px;top:1138px;font-size:9px;font-weight:600;color:#222}
.news-input{left:412px;top:1160px;width:167px;height:21px;border:1px solid #ccc;background:var(--white);font-size:8px;font-style:italic;color:#999;padding:5px 9px}
.news-input b{position:absolute;right:8px;top:2px;font-style:normal;font-size:12px;color:#666}
.follow{left:654px;top:1144px;font-size:9px;font-weight:600;color:#222}
.social{left:655px;top:1162px;display:flex;gap:7px}
.social i{display:block;width:19px;height:19px;border-radius:50%;background:#c7c7c7;border:1px solid #999}
</style>
</head>
<body>
<div class="abs logo"><span class="logo-dot"></span>Bidwell</div>
<nav class="abs top-links">
  <span>Sell</span>|<span>Sign In</span>|<span>Shopping Cart</span>
  <svg class="cart" viewBox="0 0 14 11"><path d="M1 3h12l-2 7H3z" fill="#2a9be0"/><path d="M4 3l3-3 3 3" stroke="#2a9be0" fill="none"/></svg>
  |<span>Help</span>|<span>Contact</span>
</nav>
<div class="abs search"><span>Search Entire Shop...</span><b><svg width="10" height="10" viewBox="0 0 10 10"><circle cx="4" cy="4" r="3" stroke="#fff" stroke-width="1.4" fill="none"/><path d="M6 6l3.5 3.5" stroke="#fff" stroke-width="1.6"/></svg></b></div>

<aside class="abs sidebar">
  <h2>Online Store</h2>
  <ul>
    <li>Computer</li><li>Fashion</li><li>Home &amp; Garden</li><li>Electricals &amp; Technology</li>
    <li>Collectables &amp; Antiques</li><li>Jewellery &amp; Beauty</li><li>Toys</li><li>Sport &amp; Leisure</li>
  </ul>
</aside>

<section class="abs hero">
  <div class="abs pct">40%<small>OFF</small></div>
  <div class="abs smart">The Smartest</div>
  <div class="abs cams">Cameras</div>
  <div class="abs hurry">Hurry! while supplies last</div>
  <div class="abs view">&gt; view all</div>
  <div class="abs photo" role="img" aria-label="Compact digital camera beside a tablet"></div>
  <div class="abs badge">Shop<br>Cameras</div>
</section>
<div class="abs divider"></div>

<section class="abs info">
  <div class="col welcome">
    <h3>Welcome</h3>
    <p>Even if you're new or already experienced, we have everything you need to enjoy shopping on Bidwell.</p>
    <ul>
      <li>How do I pay for items?</li><li>How do I leave feedback?</li><li>How do I open a new store?</li>
      <li>How do I place bids?</li><li>How do I ship my items?</li>
    </ul>
  </div>
  <div class="col signin">
    <h3>Sign In</h3>
    <p>Sign-in to your account in order to buy, sell or manage your preferences.</p>
    <div class="btn">Sign In</div>
    <div class="reg">Don't have an account? <b style="font-weight:400;color:#111">Register ›</b></div>
  </div>
  <div class="col confidence">
    <h3>Shop with confidence</h3>
    <div class="conf-item"><svg width="22" height="24" viewBox="0 0 22 24"><path d="M11 1l9 3v8c0 6-4 9-9 11C6 21 2 18 2 12V4z" fill="#3a9a3a"/><path d="M6 12l4 4 7-8" stroke="#fff" stroke-width="2.4" fill="none"/></svg><div><b>Completely safe</b><span>Bid on or buy items you're watching or searching for</span></div></div>
    <div class="conf-item"><svg width="22" height="24" viewBox="0 0 22 24"><path d="M5 2h12v6c0 4-3 6-6 6s-6-2-6-6z" fill="#e3b12a"/><rect x="9" y="14" width="4" height="5" fill="#c9951c"/><rect x="6" y="19" width="10" height="3" fill="#c9951c"/></svg><div><b>Completely safe</b><span>Bid on or buy items you're watching or searching for</span></div></div>
    <div class="conf-item"><svg width="22" height="24" viewBox="0 0 22 24"><rect x="1" y="5" width="20" height="8" rx="2" fill="#2a7dd8"/><path d="M13 11l4 9 1-4 4-1z" fill="#fff" stroke="#333"/></svg><div><b>Completely safe</b><span>Bid on or buy items you're watching or searching for</span></div></div>
  </div>
</section>
<div class="abs results">
  <h4>The results</h4>
  <div class="ring">success</div>
  <div class="num">11,000</div>
  <div class="strip">BANNER ADD</div>
</div>

<div class="abs bar" style="top:513px">Featured Electronics<div class="arrows"><i></i><i></i></div></div>
<div class="product" style="left:91px;top:557px"><div class="pic"><i role="img" aria-label="Flat-screen television" style="background:linear-gradient(#555,#111)"></i></div><h5>Nam fermentum</h5><p>Duis aliquam nibh a dui iaculis<br>viverra id a velit</p><div class="price">$ 220.00</div><div class="btns"><span class="add">Add Cart</span><span>Details</span></div></div>
<div class="product" style="left:259px;top:557px"><div class="pic"><i role="img" aria-label="Digital SLR camera" style="background:linear-gradient(#444,#111)"></i></div><h5>Nam fermentum</h5><p>Duis aliquam nibh a dui iaculis<br>viverra id a velit</p><div class="price">$ 350.00</div><div class="btns"><span class="add">Add Cart</span><span>Details</span></div></div>
<div class="product" style="left:426px;top:557px"><div class="pic"><i role="img" aria-label="Smartphone" style="width:48px;height:90px;background:linear-gradient(#333,#111)"></i></div><h5>Nam fermentum</h5><p>Duis aliquam nibh a dui iaculis<br>viverra id a velit</p><div class="price">$ 200.00</div><div class="btns"><span class="add">Add Cart</span><span>Details</span></div></div>
<div class="product" style="left:594px;top:557px"><div class="pic"><i role="img" aria-label="Convertible laptop" style="background:linear-gradient(#2a6fb8,#222)"></i></div><h5>Nam fermentum</h5><p>Duis aliquam nibh a dui iaculis<br>viverra id a velit</p><div class="price">$ 200.00</div><div class="btns"><span class="add">Add Cart</span><span>Details</span></div></div>

<div class="abs bar" style="top:815px">Items for Seller Store<div class="arrows"><i></i><i></i></div></div>
<div class="product" style="left:91px;top:859px"><div class="pic"><i role="img" aria-label="Tablet in a leather case" style="background:linear-gradient(#222,#3b6fa8)"></i></div><h5>Nam fermentum</h5><p>Duis aliquam nibh a dui iaculis<br>viverra id a velit</p><div class="price">$ 120.00</div><div class="btns"><span class="add">Add Cart</span><span>Details</span></div></div>
<div class="product" style="left:259px;top:859px"><div class="pic"><i role="img" aria-label="Bridge camera" style="background:linear-gradient(#444,#0e0e0e)"></i></div><h5>Nam fermentum</h5><p>Duis aliquam nibh a dui iaculis<br>viverra id a velit</p><div class="price">$ 110.00</div><div class="btns"><span class="add">Add Cart</span><span>Details</span></div></div>
<div class="product" style="left:426px;top:859px"><div class="pic"><i role="img" aria-label="Headset with microphone" style="width:70px;background:linear-gradient(#555,#111)"></i></div><h5>Nam fermentum</h5><p>Duis aliquam nibh a dui iaculis<br>viverra id a velit</p><div class="price">$ 80.00</div><div class="btns"><span class="add">Add Cart</span><span>Details</span></div></div>
<div class="product" style="left:594px;top:859px"><div class="pic"><i role="img" aria-label="Speaker set with subwoofer" style="background:linear-gradient(#666,#1a1a1a)"></i></div><h5>Nam fermentum</h5><p>Duis aliquam nibh a dui iaculis<br>viverra id a velit</p><div class="price">$ 200.00</div><div class="btns"><span class="add">Add Cart</span><span>Details</span></div></div>

<footer class="abs footer"></footer>
<div class="abs cards"><i></i><i></i><i></i></div>
<div class="abs copy">Copyright © 2014 by <b>Bidwell</b>. All Right Reserved &nbsp;|&nbsp; Privacy Policy</div>
<div class="abs news">Newsletter Sign Up</div>
<div class="abs news-input">Enter your Email..<b>›</b></div>
<div class="abs follow">Follow us on :</div>
<div class="abs social"><i></i><i></i><i></i><i></i></div>
</body>
</html>
```